Clearvale glass & hardware manufacturer

Need a SEO friendly, modern & professional looking website. We are selling all kinds of glass & accessories ( Glass/ Mirror/ splash back/ pool fence/ balustrade/ hardware...we are specialised on some special glass, like curve glass,tinted glass thermal & accoustic glass...) It should has simple & crisp feeling like a glass. It must be fully functional with product display and online ordering. Please see attached confirmed logo design(Blue & white). Make sure the theme color match its feel.

Target Market(s)

Architect and designer, Builder, & Developer

Industry/Entity Type

Manufacturer

Coding

Coded - Design and coding required

Font styles to use
Serif
Sans Serif

Colors

Designer to choose colors to be used in the design.

Requirements
Must have
• Glass & hardware theme and our logo
• Here are some competitor's website for reference. (Borrow ideas but not copy : )
• 1.https://www.tarvino.com.au/about
• 2.http://www.plumeretail.com.au/
• 3.http://www.kwd.com.au/
• 4.http://www.brackenhillfittings.com.au/
Nice to have
• Some transparent or semi transparent effects to make the website like a glass
Should not have
• No limitation for your imagination

```html
<!DOCTYPE html>
<html lang="en">
<head>
<meta charset="utf-8">
<title>Clearvale Glass &amp; Hardware</title>
<link href="https://fonts.googleapis.com/css2?family=Nunito:wght@400;600;700&family=Open+Sans:wght@400;600&family=Rajdhani:wght@600&display=swap" rel="stylesheet">
<style>
:root{
  --brand:#1b8fd9;
  --brand-dark:#1a5fa8;
  --ink:#1d1d1f;
  --muted:#555;
  --line:#b9c2cc;
  --footer-bar:#d8d8d8;
  --white:#fff;
}
*{margin:0;padding:0;box-sizing:border-box}
html,body{width:1200px;height:2913px;overflow:hidden}
body{position:relative;background:var(--white);font-family:"Open Sans",Arial,sans-serif;color:var(--ink)}
.abs{position:absolute}
a{color:inherit;text-decoration:none}

.topbar{left:0;top:0;width:1200px;height:33px;background:var(--brand);color:var(--white);font-size:12px;font-weight:600;text-transform:uppercase}
.topbar span{position:absolute;top:8px;display:flex;align-items:center;gap:7px}
.topbar svg{width:14px;height:14px}

.header{left:0;top:33px;width:1200px;height:107px;background:var(--white)}
.brand{position:absolute;left:115px;top:30px;display:flex;align-items:center;gap:12px;font-family:"Nunito",sans-serif;font-weight:700;font-size:34px;line-height:46px;color:var(--brand-dark);letter-spacing:1px;white-space:nowrap}
.brand i{display:block;width:40px;height:40px;background:var(--brand)}
.nav a{position:absolute;top:50px;font-family:"Nunito",sans-serif;font-size:16px;color:#333;text-transform:uppercase;white-space:nowrap}
.nav a.active{color:var(--brand)}

.hero{left:0;top:140px;width:1200px;height:569px;background:linear-gradient(160deg,#dfe6ee 0%,#9aa9bb 40%,#e8ecf1 60%,#8a99ab 100%)}
.hero-panel{position:absolute;left:120px;top:60px}
.hero-title{position:absolute;left:176px;top:160px;font-family:"Rajdhani",sans-serif;font-weight:600;font-size:62px;line-height:64px;color:var(--brand);text-transform:uppercase}
.hero-title span{color:var(--brand-dark)}
.dots{position:absolute;left:555px;top:513px;display:flex;gap:10px}
.dots i{width:14px;height:14px;border-radius:50%;background:#222;border:2px solid #222}
.dots i:first-child{background:transparent}

.section-title{position:absolute;left:0;width:1200px;text-align:center;font-family:"Nunito",sans-serif;font-weight:600;font-size:28px;color:#111;text-transform:uppercase}
.divider{position:absolute;left:438px;width:324px;height:16px}
.divider:before{content:"";position:absolute;left:0;right:0;top:8px;height:1px;background:var(--line)}
.divider:after{content:"";position:absolute;left:153px;top:0;width:18px;height:18px;background:var(--brand);transform:rotate(45deg)}

.card{position:absolute;overflow:hidden}
.card .label{position:absolute;left:0;right:0;background:rgba(27,143,217,.85);color:var(--white);text-align:center;text-transform:uppercase;white-space:nowrap}
.special .card{top:833px;width:306px;height:286px}
.special .label{top:212px;height:46px;line-height:46px;font-family:"Nunito",sans-serif;font-size:20px}

.about{left:0;top:1185px;width:1200px;height:478px;background:linear-gradient(90deg,#1f5fa8 0%,#7cb8e6 30%,#cfe3f3 55%,#e9eaec 62%,#d3d5d8 100%)}
.about-copy{position:absolute;left:732px;top:108px;width:350px}
.about h2{font-family:"Nunito",sans-serif;font-weight:600;font-size:31px;line-height:34px;text-transform:uppercase}
.about h3{font-family:"Nunito",sans-serif;font-weight:700;font-size:25px;line-height:30px;text-transform:uppercase}
.body-text{font-size:14px;line-height:20px;color:#333;margin-top:18px}
.btn{display:inline-block;background:var(--brand);color:var(--white);font-size:16px;text-transform:uppercase;text-align:center}

.hardware .card{top:1820px;width:217px;height:233px}
.hardware .label{top:177px;height:38px;line-height:38px;font-size:16px}
.arrow{position:absolute;top:1900px;width:28px;height:70px}

.why{left:0;top:2105px;width:1200px;height:429px;background:linear-gradient(180deg,#4a9ee0 0%,#9fcdf0 45%,#dceefa 100%)}
.why h2{position:absolute;left:153px;top:102px;font-family:"Nunito",sans-serif;font-weight:600;font-size:28px;text-transform:uppercase}
.why .body-text{position:absolute;left:153px;top:145px;width:360px;margin:0}
.why-visual{position:absolute;left:650px;top:20px;width:420px;height:400px;border-radius:8px;background:linear-gradient(120deg,rgba(255,255,255,.6),rgba(200,225,240,.4))}

.footer{left:0;top:2534px;width:1200px;height:311px;background:var(--white)}
.footer .brand{left:132px;top:86px;font-size:30px}
.footer .brand i{width:36px;height:36px}
.social{position:absolute;left:140px;top:180px;display:flex;gap:8px}
.social i{width:38px;height:38px;border-radius:50%;background:var(--brand)}
.fcol{position:absolute;top:78px;font-size:15px;color:#666}
.fcol h4{font-family:"Nunito",sans-serif;font-weight:700;font-size:19px;color:var(--brand);text-transform:uppercase;margin-bottom:16px}
.fcol li{list-style:none;line-height:31px;white-space:nowrap}
.contact li{display:flex;align-items:flex-start;gap:10px}
.contact svg{width:16px;height:16px;margin-top:7px;flex:none}
.bottombar{left:0;top:2845px;width:1200px;height:68px;background:var(--footer-bar);text-align:center;line-height:68px;font-size:13px;color:#444}
</style>
</head>
<body>

<div class="abs topbar">
  <span style="left:130px"><svg viewBox="0 0 16 16"><circle cx="6.5" cy="6.5" r="4.5" fill="none" stroke="#fff" stroke-width="2"/><path d="M10 10l4.5 4.5" stroke="#fff" stroke-width="2"/></svg>Search here</span>
  <span style="left:672px"><svg viewBox="0 0 16 16"><path d="M3 1l3 3-1.5 2a9 9 0 0 0 5.5 5.5L12 10l3 3-2 2C7 15 1 9 1 3z" fill="#fff"/></svg>Call us today: 666-555-0182</span>
  <span style="left:905px;text-transform:none"><svg viewBox="0 0 16 16"><rect x="1" y="3" width="14" height="10" fill="#fff"/><path d="M1 3l7 6 7-6" fill="none" stroke="#1b8fd9" stroke-width="1.5"/></svg>hello@clearvale-glass.com</span>
</div>

<header class="abs header">
  <div class="brand"><i></i>CLEARVALE</div>
  <nav class="nav">
    <a class="active" style="left:452px">Home</a>
    <a style="left:527px">Products</a>
    <a style="left:643px">Hardware</a>
    <a style="left:763px">Glass</a>
    <a style="left:843px">News</a>
    <a style="left:920px">Blog</a>
    <a style="left:991px">Contact</a>
  </nav>
</header>

<section class="abs hero" role="img" aria-label="Looking up into a curved glass atrium with a triangulated glass roof">
  <svg class="hero-panel" width="420" height="440" viewBox="0 0 420 440"><polygon points="210,0 420,110 420,330 210,440 0,330 0,110" fill="rgba(255,255,255,.55)"/></svg>
  <h1 class="hero-title">Clearvale<br><span>Glass &amp;<br>Hardwares</span></h1>
  <div class="dots"><i></i><i></i><i></i><i></i></div>
</section>

<section class="special">
  <h2 class="section-title" style="top:738px">Special Glass</h2>
  <div class="divider" style="top:786px"></div>
  <div class="card" style="left:120px;background:linear-gradient(135deg,#2f7fd0,#b8d6f0 60%,#7fa8cf)" role="img" aria-label="Curved glass facade against blue sky"><div class="label">Curve Glass</div></div>
  <div class="card" style="left:449px;background:linear-gradient(135deg,#1e5eb8,#5c9fe0 50%,#a9cff2)" role="img" aria-label="Tinted glass building reflecting trees"><div class="label">Tinted Glass Thermal</div></div>
  <div class="card" style="left:775px;background:linear-gradient(180deg,#2b6fd1,#7ab3ea 55%,#1e3566)" role="img" aria-label="Acoustic glass panels along a highway at dusk"><div class="label">Acoustic Glass</div></div>
</section>

<section class="abs about" role="img" aria-label="Blue curved glass walkway tunnel">
  <div class="about-copy">
    <h2>About Clearvale</h2>
    <h3>Glass &amp; Hardwares</h3>
    <p class="body-text">Vivamus porttitor purus nisi eleifend libero a tempus libero lectus feugiat felis Morbi diam mauris</p>
    <p class="body-text" style="margin-top:14px">Morbi porta Aibero id ullamcorper nonummy nibh ligula pulvinar metus eget consectetuer augue nisi quis lacus Ut ac mi quis lacus mollis aliquam Curabitur iaculis tempus eros</p>
    <a class="btn" style="width:161px;height:42px;line-height:42px;margin-top:22px">Learn More</a>
  </div>
</section>

<section class="hardware">
  <h2 class="section-title" style="top:1730px">Hard Ware &amp; Products</h2>
  <div class="divider" style="top:1778px"></div>
  <svg class="arrow" style="left:104px" viewBox="0 0 28 70"><path d="M26 2L3 35l23 33" fill="none" stroke="#1b8fd9" stroke-width="3"/><path d="M22 22L12 35l10 13" fill="none" stroke="#333" stroke-width="3"/></svg>
  <svg class="arrow" style="left:1066px" viewBox="0 0 28 70"><path d="M2 2l23 33L2 68" fill="none" stroke="#1b8fd9" stroke-width="3"/><path d="M6 22l10 13L6 48" fill="none" stroke="#333" stroke-width="3"/></svg>
  <div class="card" style="left:142px;background:linear-gradient(135deg,#e9ecef,#c7ccd2)" role="img" aria-label="Frameless glass office partition"><div class="label">Glass</div></div>
  <div class="card" style="left:377px;background:linear-gradient(135deg,#d8f2a8,#6cc13a 60%,#b8e67d)" role="img" aria-label="Green glass splashback tiles"><div class="label">Splash Back</div></div>
  <div class="card" style="left:608px;background:linear-gradient(180deg,#b9d5ea,#5fb6e0 55%,#2a8fcf)" role="img" aria-label="Glass pool fence beside a swimming pool"><div class="label">Pool Fence</div></div>
  <div class="card" style="left:841px;background:linear-gradient(180deg,#dfe5e9,#8d9aa3 60%,#5a4a3a)" role="img" aria-label="Glass balustrade on a stairway landing"><div class="label">Balustrade</div></div>
</section>

<section class="abs why">
  <h2>Why Our Products</h2>
  <div class="body-text">
    <p>Vivamus porttitor purus nisi eleifend libero a tempus libero lectus feugiat felis Morbi diam mauris</p>
    <p style="margin-top:10px">Morbi porta Aibero id ullamcorper nonummy nibh ligula pulvinar metus eget consectetuer augue nisi quis lacus Ut ac mi quis lacus mollis aliquam Curabitur iaculis tempus eros</p>
  </div>
  <a class="btn abs" style="left:148px;top:303px;width:161px;height:41px;line-height:41px">Learn More</a>
  <div class="why-visual" role="img" aria-label="Curved clear glass panels standing in a row"></div>
</section>

<footer class="abs footer">
  <div class="brand"><i></i>CLEARVALE</div>
  <div class="social" aria-label="Social links"><i></i><i></i><i></i><i></i></div>
  <div class="fcol" style="left:464px">
    <h4>Quick Links</h4>
    <ul><li>Home</li><li>About Us</li><li>Products</li><li>Why Us</li></ul>
  </div>
  <div class="fcol" style="left:660px;top:72px">
    <h4>Resources</h4>
    <ul><li>Curve glass</li><li>Tinted glass thermal</li><li>Acoustic glass</li><li>Glass &amp; Mirror</li></ul>
  </div>
  <div class="fcol contact" style="left:872px;top:70px">
    <h4>Contact Us</h4>
    <ul>
      <li><svg viewBox="0 0 16 16"><path d="M8 1a5 5 0 0 1 5 5c0 4-5 9-5 9S3 10 3 6a5 5 0 0 1 5-5z" fill="#1b8fd9"/><circle cx="8" cy="6" r="2" fill="#fff"/></svg><span>48 Harbour Lane Suite 3<br>Portland 97204 OR</span></li>
      <li><svg viewBox="0 0 16 16"><path d="M3 1l3 3-1.5 2a9 9 0 0 0 5.5 5.5L12 10l3 3-2 2C7 15 1 9 1 3z" fill="none" stroke="#1b8fd9" stroke-width="1.4"/></svg>555.214.0937</li>
      <li><svg viewBox="0 0 16 16"><rect x="1" y="3" width="14" height="10" fill="none" stroke="#1b8fd9" stroke-width="1.4"/><path d="M1 3l7 6 7-6" fill="none" stroke="#1b8fd9" stroke-width="1.4"/></svg>hello@clearvale-glass.com</li>
    </ul>
  </div>
</footer>

<div class="abs bottombar">© 2018 Clearvale Glass&nbsp; All right reserved</div>

</body>
</html>
```